Harbor Crestline (Business Card Design)

Need business cards designed. Something modern, chic, and sleek. Mabye the back of the card should be the navy blue that is in the logo and then just the logo on the back.

Target Market(s)

Those in the hotel, office, and renovation industry

Contact Information for Business Card

1. Logo 2. Dorian Fenwick 3. CEO/Founder 4. Phone: (833) HarbCre / (833) 427-2731 5. Email: dorian@theharborcrestline.com 6. Website: www.theharborcrestline.com

Font styles to use
Other font styles liked:
• Look at the logo font and base the font for everything else off of that.

Colors
0054AA
0677BA
7BADD7
CADEEF
E8F1F8

Requirements
Must have
• Colors that are associated in the logo
Nice to have
• Sleek modern clean and chic design.

```html
<!DOCTYPE html>
<html lang="en">
<head>
<meta charset="utf-8">
<title>Harbor Crestline — Business Card</title>
<link rel="stylesheet" href="https://fonts.googleapis.com/css2?family=Montserrat:wght@600;700&family=Open+Sans:wght@400;600&display=swap">
<style>
  :root {
    --stage: #2a2d33;
    --paper: #ffffff;
    --navy: #141c4a;
    --navy-deep: #0d1338;
    --navy-light: #26306b;
    --gold: #c9a040;
    --ink: #111111;
    --rule: #2b2b2b;
  }
  html, body {
    margin: 0;
    width: 1200px;
    height: 780px;
    overflow: hidden;
    background: var(--stage);
  }
  .canvas {
    position: relative;
    width: 1200px;
    height: 780px;
    display: flex;
    align-items: center;
    justify-content: center;
    gap: 40px;
  }
  .card {
    position: relative;
    width: 560px;
    height: 320px;
    border-radius: 22px;
    overflow: hidden;
    box-shadow: 0 10px 30px rgba(0,0,0,0.35);
  }

  /* Front */
  .card-front { background: var(--paper); }
  .brand {
    position: absolute;
    left: 40px;
    top: 38px;
    display: flex;
    align-items: center;
    gap: 12px;
  }
  .brand-square {
    width: 26px;
    height: 26px;
    background: var(--navy);
  }
  .brand-name {
    font-family: "Montserrat", sans-serif;
    font-weight: 700;
    font-size: 20px;
    letter-spacing: 1.5px;
    color: var(--navy);
    text-transform: uppercase;
  }
  .divider {
    position: absolute;
    left: 42px;
    top: 176px;
    width: 430px;
    height: 1.5px;
    background: var(--rule);
  }
  .identity {
    position: absolute;
    right: 98px;
    top: 106px;
    text-align: right;
  }
  .person-name {
    font-family: "Montserrat", sans-serif;
    font-weight: 700;
    font-size: 32px;
    line-height: 1;
    margin: 0;
  }
  .person-name .first { color: var(--gold); }
  .person-name .last { color: var(--ink); }
  .person-title {
    font-family: "Open Sans", sans-serif;
    font-size: 15px;
    color: var(--ink);
    margin: 6px 0 0;
  }
  .gold-steps { position: absolute; right: 0; top: 160px; }
  .gold-steps span {
    display: block;
    background: var(--gold);
    margin-left: auto;
  }
  .gold-steps .s1 { width: 92px; height: 26px; }
  .gold-steps .s2 { width: 80px; height: 26px; }
  .gold-steps .s3 { width: 66px; height: 26px; }

  .contact {
    position: absolute;
    left: 40px;
    top: 192px;
    font-family: "Open Sans", sans-serif;
    font-size: 12.5px;
    line-height: 19px;
    color: var(--ink);
    margin: 0;
    padding: 0;
    list-style: none;
  }
  .contact li { display: flex; align-items: center; gap: 7px; }
  .contact .address { padding-left: 0; }
  .contact .icon { width: 11px; height: 11px; flex: none; }

  /* Back */
  .card-back {
    background: linear-gradient(120deg, var(--navy-deep) 0%, var(--navy) 55%, var(--navy-light) 100%);
  }
  .back-pattern {
    position: absolute;
    inset: 0;
    background: linear-gradient(120deg, rgba(255,255,255,0) 40%, rgba(170,180,230,0.18) 100%);
  }
  .back-brand {
    position: absolute;
    right: 44px;
    bottom: 40px;
    display: flex;
    align-items: center;
    gap: 9px;
  }
  .back-brand .brand-square { width: 16px; height: 16px; background: #ffffff; }
  .back-brand .brand-name { font-size: 14px; color: #ffffff; }
</style>
</head>
<body>
<main class="canvas">

  <section class="card card-front" aria-label="Business card front">
    <div class="brand">
      <span class="brand-square"></span>
      <span class="brand-name">Harbor Crestline</span>
    </div>

    <div class="identity">
      <h1 class="person-name"><span class="first">Dorian</span> <span class="last">Fenwick</span></h1>
      <p class="person-title">CEO/Founder</p>
    </div>

    <div class="divider"></div>

    <div class="gold-steps" aria-hidden="true">
      <span class="s1"></span><span class="s2"></span><span class="s3"></span>
    </div>

    <ul class="contact">
      <li class="address">4120 Linden Ridge Rd</li>
      <li class="address">Suite 210, Brookhaven, MD 21390</li>
      <li>
        <svg class="icon" viewBox="0 0 12 12" aria-hidden="true"><path d="M2.5 1h2l1 2.6-1.3 1a6 6 0 0 0 3.2 3.2l1-1.3 2.6 1v2a1 1 0 0 1-1 1A9.5 9.5 0 0 1 1.5 2a1 1 0 0 1 1-1z" fill="var(--gold)"/></svg>
        (833) HarbCre / (833) 427-2731
      </li>
      <li>
        <svg class="icon" viewBox="0 0 12 12" aria-hidden="true"><circle cx="6" cy="6" r="5" fill="none" stroke="var(--gold)" stroke-width="1.3"/><path d="M1 6h10M6 1c2 2.5 2 7.5 0 10M6 1c-2 2.5-2 7.5 0 10" fill="none" stroke="var(--gold)" stroke-width="1"/></svg>
        www.theharborcrestline.com
      </li>
      <li>
        <svg class="icon" viewBox="0 0 12 12" aria-hidden="true"><rect x="0.8" y="2.2" width="10.4" height="7.6" rx="1" fill="none" stroke="var(--gold)" stroke-width="1.3"/><path d="M1 3l5 3.6L11 3" fill="none" stroke="var(--gold)" stroke-width="1.2"/></svg>
        dorian@theharborcrestline.com
      </li>
    </ul>
  </section>

  <section class="card card-back" aria-label="Business card back">
    <div class="back-pattern" role="img" aria-label="Repeating brand pattern on navy, fading lighter toward the right"></div>
    <div class="back-brand">
      <span class="brand-square"></span>
      <span class="brand-name">Harbor Crestline</span>
    </div>
  </section>

</main>
</body>
</html>
```